New Business Card Design for Manufacturing

We are an engineering/manufacturing company that offers Advanced machining/assembly/engineering services, as well as innovative products for the heavy duty engine cooling markets.

We are looking to get a new business card designed that is clean and modern looking, but still fits the wide range of technical/skilled work we do.

- We hope to use this design as the base for other design work in new Presentations, web, and print work.

Industry/Entity Type

Engineering

Contact Information for Business Card

Our preferred color of blue is (RGB) 22/71/159 but can vary slightly from that color. Our content will be our Logo and full company name (Vantrell Forge Works, Inc.), company address, name, job title, phone number with extension, cell number, fax number, website, and email address on the cards.
We'd like the full company name next to the logo, but we are open to other interpretations of that layout.
Preferably, we would like the back side to be clean with just our logo, and the front to contain all of the contact information.

Colors
2f74b4
0355a3
85abd2

Requirements
Must have
• - Logo, company name, needed content - We are open to interpretation beyond that.
• - Standard size business card.
• - Horizontal orientation.
• - Enough space for lengthy names / job titles (for example, a job title could read "Directory of Human Resources" or "V.P. of Governmental Affairs"). We need this to look clean, whether the title be short (CEO) or long (as described above).

```html
<!DOCTYPE html>
<html lang="en">
<head>
<meta charset="utf-8">
<title>Vantrell Forge Works – Business Card</title>
<link href="https://fonts.googleapis.com/css2?family=Montserrat:wght@500;600&family=Open+Sans:wght@400;600&display=swap" rel="stylesheet">
<style>
  :root {
    --backdrop: #3a3a3a;
    --card: #1d1d1f;
    --card-edge: #151516;
    --mark-dark: #2e2e30;
    --brand-blue: #0f6fc6;
    --rule-blue: #0355a3;
    --text-light: #f2f2f2;
  }
  * { margin: 0; padding: 0; box-sizing: border-box; }
  html, body { width: 799px; height: 1200px; overflow: hidden; }
  body {
    background: var(--backdrop);
    font-family: "Open Sans", Arial, sans-serif;
    color: var(--text-light);
    position: relative;
  }
  .card {
    position: absolute;
    left: 60px;
    width: 680px;
    height: 390px;
    background: var(--card);
    border: 1px solid var(--card-edge);
    box-shadow: 0 18px 40px rgba(0,0,0,.45);
  }
  .card--back { top: 140px; }
  .card--front { top: 670px; }

  /* back side */
  .back-mark {
    position: absolute; inset: 0;
    display: flex; align-items: center; justify-content: center; gap: 18px;
  }
  .back-mark__square { width: 30px; height: 30px; background: var(--mark-dark); }
  .back-mark__name {
    font-family: "Open Sans", Arial, sans-serif;
    font-weight: 600; font-size: 46px; letter-spacing: 1px;
    color: var(--mark-dark);
  }

  /* front side */
  .front-mark {
    position: absolute; top: 46px; left: 0; right: 0;
    text-align: center;
    font-weight: 600; font-size: 40px; letter-spacing: 1px;
    color: var(--brand-blue);
  }
  .company-row {
    position: absolute; top: 122px; left: 40px; right: 40px;
    display: flex; align-items: center; gap: 16px;
  }
  .company-row__rule { flex: 1; height: 2px; background: var(--rule-blue); }
  .company-row__name {
    font-family: "Montserrat", Arial, sans-serif;
    font-weight: 600; font-size: 21px; color: var(--text-light);
  }
  .person {
    position: absolute; top: 172px; left: 40px; width: 290px;
    text-align: right;
  }
  .person__name { font-size: 27px; color: var(--brand-blue); line-height: 1.15; }
  .person__title { font-size: 14px; line-height: 1.3; margin-top: 6px; }
  .divider {
    position: absolute; top: 176px; left: 350px;
    width: 1.5px; height: 112px; background: var(--rule-blue);
  }
  .contacts {
    position: absolute; top: 170px; left: 372px;
    list-style: none; font-size: 15px; line-height: 24px;
  }
  .contacts li { display: flex; align-items: center; gap: 12px; }
  .contacts svg { width: 14px; height: 14px; fill: var(--brand-blue); flex: none; }
  .contacts .web-accent { color: var(--brand-blue); }
  .address {
    position: absolute; top: 312px; left: 0; right: 0;
    text-align: center; font-size: 16px;
  }
  .bottom-rule {
    position: absolute; top: 352px; left: 40px; right: 40px;
    height: 2px; background: var(--rule-blue);
  }
</style>
</head>
<body>

<section class="card card--back" aria-label="Card back">
  <div class="back-mark">
    <span class="back-mark__square"></span>
    <span class="back-mark__name">VANTRELL</span>
  </div>
</section>

<section class="card card--front" aria-label="Card front">
  <div class="front-mark">VANTRELL</div>

  <div class="company-row">
    <span class="company-row__rule"></span>
    <span class="company-row__name">Vantrell Forge Works, Inc.</span>
    <span class="company-row__rule"></span>
  </div>

  <div class="person">
    <p class="person__name">Dana Keller</p>
    <p class="person__title">Managing Director / Admin /<br>PhD Holder / Owner /<br>Technician / Developer / Producer</p>
  </div>

  <div class="divider"></div>

  <ul class="contacts">
    <li><svg viewBox="0 0 16 16"><path d="M3 1h3l1.5 4-2 1.3a9 9 0 0 0 4.2 4.2L11 8.5l4 1.5v3a2 2 0 0 1-2 2A12 12 0 0 1 1 3a2 2 0 0 1 2-2z"/></svg>555-0142-2140 (Ext. 214)</li>
    <li><svg viewBox="0 0 16 16"><path d="M4 0h8a1 1 0 0 1 1 1v14a1 1 0 0 1-1 1H4a1 1 0 0 1-1-1V1a1 1 0 0 1 1-1zm1 2v10h6V2zm3 11a1 1 0 1 0 0 2 1 1 0 0 0 0-2z"/></svg>555-0187-3361</li>
    <li><svg viewBox="0 0 16 16"><path d="M4 0h7l1 1v4H4zM1 6h14a1 1 0 0 1 1 1v6h-3v3H3v-3H0V7a1 1 0 0 1 1-1zm4 6v3h6v-3z"/></svg>555-0142-2199</li>
    <li><svg viewBox="0 0 16 16"><path d="M0 3h16v10H0zm1.5 1.2V5l6.5 4.3L14.5 5v-.8L8 8.3z"/></svg>dana.keller@vantrellforge.com</li>
    <li><svg viewBox="0 0 16 16"><path d="M8 0a8 8 0 1 0 0 16A8 8 0 0 0 8 0zm5.9 7h-2.5a12 12 0 0 0-1-4.6A6 6 0 0 1 13.9 7zM8 2c.8.9 1.3 2.7 1.4 5H6.6C6.7 4.7 7.2 2.9 8 2zM5.6 2.4A12 12 0 0 0 4.6 7H2.1a6 6 0 0 1 3.5-4.6zM2.1 9h2.5a12 12 0 0 0 1 4.6A6 6 0 0 1 2.1 9zM8 14c-.8-.9-1.3-2.7-1.4-5h2.8c-.1 2.3-.6 4.1-1.4 5zm2.4-.4a12 12 0 0 0 1-4.6h2.5a6 6 0 0 1-3.5 4.6z"/></svg>www.<span class="web-accent">vantrellforge</span>.com</li>
  </ul>

  <p class="address">1180 Foundry Road, Millbrook, OH 44720</p>
  <div class="bottom-rule"></div>
</section>

</body>
</html>
```